Quillmarsh Property Solutions need a business card design

Hello guys. We would need a business card design asap please.
We are a start up property investment business based in London UK specialised in buying, selling, managing and letting properties and helping distressed property owners.
The name of our Business is Quillmarsh, the logo symbolises the four fundamental elements of the world (earth, air, fire and water) and so it stands for strength, stability, longevity.
We would like the business card to communicate professionalism and reliability. Many many thanks indeed for your work.

Details:

1.) Rosalind Updike
Property Investor
Mobile: +44(0)7700123456
Email: rosalind.quillmarsh@mailbox-example.com

2.) Dominic Updike
Property Investor
Mobile: +44(0)7700987654
Email: dominic.quillmarsh@mailbox-example.com

```html
<!DOCTYPE html>
<html lang="en">
<head>
<meta charset="utf-8">
<title>Quillmarsh Property Solutions – Business Card</title>
<link rel="stylesheet" href="https://fonts.googleapis.com/css2?family=Jost:wght@500;600;700&family=Open+Sans:wght@400;600&display=swap">
<style>
  :root {
    --backdrop: #efece8;
    --card-white: #ffffff;
    --brand-red: #c0283a;
    --brand-blue: #2b4aa0;
    --ink: #1d1d1f;
    --on-red: #ffffff;
    --card-shadow: 0 10px 28px rgba(0, 0, 0, 0.16);
  }
  * { box-sizing: border-box; margin: 0; padding: 0; }
  html, body {
    width: 1200px;
    height: 720px;
    overflow: hidden;
    background: var(--backdrop);
  }
  .canvas {
    position: relative;
    width: 1200px;
    height: 720px;
    display: flex;
    align-items: center;
    justify-content: center;
    gap: 40px;
  }
  .card {
    position: relative;
    width: 540px;
    height: 309px;
    border-radius: 4px;
    overflow: hidden;
    box-shadow: var(--card-shadow);
  }

  /* Front */
  .card--front { background: var(--card-white); }
  .card__curve {
    position: absolute;
    inset: 0;
    width: 100%;
    height: 100%;
  }
  .brand {
    position: absolute;
    top: 58px;
    left: 0;
    right: 0;
    display: flex;
    align-items: center;
    justify-content: center;
    gap: 12px;
  }
  .brand__mark {
    width: 30px;
    height: 30px;
    background: var(--brand-red);
  }
  .brand__name {
    font-family: "Jost", sans-serif;
    font-weight: 700;
    color: var(--ink);
    line-height: 1.05;
    text-transform: uppercase;
  }
  .brand__name-main {
    display: block;
    font-size: 26px;
    letter-spacing: 0.5px;
  }
  .brand__name-sub {
    display: block;
    font-size: 10.5px;
    letter-spacing: 1.6px;
  }
  .contact-strip {
    position: absolute;
    left: 28px;
    right: 20px;
    bottom: 34px;
    display: flex;
    align-items: center;
    gap: 14px;
    color: var(--on-red);
  }
  .person__name {
    font-family: "Jost", sans-serif;
    font-weight: 600;
    font-size: 18px;
    line-height: 1.2;
  }
  .person__role {
    font-family: "Open Sans", sans-serif;
    font-size: 12px;
    line-height: 1.3;
  }
  .contact-strip__divider {
    width: 1.5px;
    height: 42px;
    background: var(--on-red);
  }
  .contact-list {
    list-style: none;
    font-family: "Open Sans", sans-serif;
    font-size: 11.5px;
    line-height: 1.75;
  }
  .contact-list__item {
    display: flex;
    align-items: center;
    gap: 7px;
  }
  .contact-list__icon {
    width: 11px;
    height: 11px;
    flex: none;
  }

  /* Back */
  .card--back {
    background: var(--brand-red);
    display: flex;
    flex-direction: column;
    align-items: center;
    justify-content: center;
    color: var(--on-red);
    font-family: "Jost", sans-serif;
    font-weight: 700;
    text-transform: uppercase;
  }
  .back__name {
    font-size: 50px;
    letter-spacing: 1.5px;
    line-height: 1;
  }
  .back__tagline {
    margin-top: 10px;
    font-size: 23px;
    letter-spacing: 1px;
    line-height: 1;
  }
</style>
</head>
<body>
<main class="canvas">

  <section class="card card--front" aria-label="Business card front">
    <svg class="card__curve" viewBox="0 0 540 309" preserveAspectRatio="none" aria-hidden="true">
      <path d="M0,236 Q250,140 540,128 L540,309 L0,309 Z" fill="var(--brand-red)"/>
      <path d="M0,226 Q250,128 540,116" fill="none" stroke="var(--brand-blue)" stroke-width="4"/>
    </svg>

    <div class="brand">
      <span class="brand__mark" aria-hidden="true"></span>
      <p class="brand__name">
        <span class="brand__name-main">Quillmarsh</span>
        <span class="brand__name-sub">Property Solutions</span>
      </p>
    </div>

    <div class="contact-strip">
      <div class="person">
        <p class="person__name">Dominic Updike</p>
        <p class="person__role">Property Investor</p>
      </div>
      <span class="contact-strip__divider" aria-hidden="true"></span>
      <ul class="contact-list">
        <li class="contact-list__item">
          <svg class="contact-list__icon" viewBox="0 0 12 12" aria-hidden="true">
            <rect x="3" y="0.5" width="6" height="11" rx="1.2" fill="none" stroke="currentColor" stroke-width="1.2"/>
            <circle cx="6" cy="9.4" r="0.8" fill="currentColor"/>
          </svg>
          <span>+44(0)7700987654</span>
        </li>
        <li class="contact-list__item">
          <svg class="contact-list__icon" viewBox="0 0 12 12" aria-hidden="true">
            <rect x="0.6" y="2.2" width="10.8" height="7.6" rx="0.8" fill="none" stroke="currentColor" stroke-width="1.2"/>
            <path d="M1,2.8 L6,6.8 L11,2.8" fill="none" stroke="currentColor" stroke-width="1.2"/>
          </svg>
          <span>dominic.quillmarsh@mailbox-example.com</span>
        </li>
      </ul>
    </div>
  </section>

  <section class="card card--back" aria-label="Business card back">
    <p class="back__name">Quillmarsh</p>
    <p class="back__tagline">Property Solutions</p>
  </section>

</main>
</body>
</html>
```